Support People to improve their image and well-being by provided personalised advise

We need a design for business cards that could be used for production on plano press. We build a new business in our region for advising mostly women (also men though) on style embracing several aspects including fashion, style, self-confidence and ultimately your internal and external image. The business card should be "classy", "french-style". The business is located in the french -speaking part of Switzerland, close to France. The name of the company is Lomu Grace

Target Market(s)

Service fees won't be cheap (medium to premium) thus we target mid-class to upper-class women (1st target) and men (2nd target)

Industry/Entity Type

Life Coaching

Contact Information for Business Card

Conseil en Image

+41 76 418 63 07
tovasel@lomu-grace.example
linkedin.example/in/sel-moran-tova

Logo Text

Lomu Grace

Colors

Designer to choose colors to be used in the design.

```html
<!DOCTYPE html>
<html lang="fr">
<head>
<meta charset="utf-8">
<title>Lomu Grace – Business Cards</title>
<link rel="stylesheet" href="https://fonts.googleapis.com/css2?family=Jost:wght@400;500&family=Caveat+Brush&display=swap">
<style>
  :root {
    --backdrop: #bfbfbf;
    --card-dark: #363a3d;
    --card-light: #f4f4f3;
    --gold-light: #e6c894;
    --gold-deep: #b08e66;
    --gold-text: #bb956a;
    --ink: #3a3e41;
    --ink-soft: #4a4d50;
    --silver: #cfcbc6;
  }
  * { box-sizing: border-box; margin: 0; padding: 0; }
  html, body {
    width: 1200px;
    height: 576px;
    overflow: hidden;
    background: var(--backdrop);
  }
  .canvas {
    position: relative;
    width: 1200px;
    height: 576px;
  }
  .card {
    position: absolute;
    top: 139px;
    width: 484px;
    height: 294px;
    border-radius: 14px;
    overflow: hidden;
  }
  .card--front {
    left: 82px;
    background: var(--card-dark);
  }
  .card--back {
    left: 602px;
    width: 480px;
    height: 292px;
    background: var(--card-light);
  }

  /* Front */
  .front-mark {
    position: absolute;
    left: 50%;
    top: 88px;
    width: 54px;
    height: 54px;
    margin-left: -27px;
    border-radius: 50%;
    background: linear-gradient(160deg, var(--gold-light), var(--gold-deep));
  }
  .front-name {
    position: absolute;
    left: 0;
    right: 0;
    top: 180px;
    text-align: center;
    font-family: "Jost", sans-serif;
    font-weight: 400;
    font-size: 25px;
    line-height: 30px;
    letter-spacing: 4px;
    color: var(--silver);
    text-transform: uppercase;
  }

  /* Back */
  .back-monogram {
    position: absolute;
    left: 38px;
    top: 28px;
    width: 74px;
    bottom: 0;
    border-radius: 8px 8px 0 0;
    background: linear-gradient(180deg, var(--gold-light), var(--gold-deep));
  }
  .back-brand {
    position: absolute;
    left: 262px;
    top: 50px;
    font-family: "Jost", sans-serif;
    font-weight: 400;
    font-size: 23px;
    line-height: 28px;
    letter-spacing: 3px;
    color: var(--ink);
    text-transform: uppercase;
    white-space: nowrap;
  }
  .person-name {
    position: absolute;
    left: 262px;
    top: 130px;
    font-family: "Caveat Brush", cursive;
    font-size: 23px;
    line-height: 28px;
    color: var(--gold-text);
    letter-spacing: 0.5px;
  }
  .person-role {
    position: absolute;
    left: 262px;
    top: 161px;
    font-family: "Jost", sans-serif;
    font-size: 12.5px;
    line-height: 16px;
    color: var(--ink-soft);
  }
  .contact-list {
    position: absolute;
    left: 262px;
    top: 196px;
    list-style: none;
    font-family: "Jost", sans-serif;
    font-size: 13px;
    color: var(--ink-soft);
  }
  .contact-item {
    display: flex;
    align-items: center;
    height: 18px;
    white-space: nowrap;
  }
  .contact-icon {
    width: 11px;
    height: 11px;
    margin-right: 13px;
    fill: var(--ink);
    flex: none;
  }
</style>
</head>
<body>
<main class="canvas">
  <section class="card card--front" aria-label="Card front">
    <div class="front-mark" aria-hidden="true"></div>
    <p class="front-name">Lomu Grace</p>
  </section>

  <section class="card card--back" aria-label="Card back">
    <div class="back-monogram" role="img" aria-label="Large gold brand monogram decoration"></div>
    <p class="back-brand">Lomu Grace</p>
    <p class="person-name">Tova Moran</p>
    <p class="person-role">Conseil en Image</p>
    <ul class="contact-list">
      <li class="contact-item">
        <svg class="contact-icon" viewBox="0 0 12 12" aria-hidden="true">
          <path d="M1 4.2C1 2.5 3 1.5 6 1.5s5 1 5 2.7v.8H8.6V3.9c-.7-.3-1.6-.4-2.6-.4s-1.9.1-2.6.4V5H1z"/>
          <path d="M3.6 5.4h4.8L10 8.6V10.5H2V8.6z"/>
        </svg>
        +41 00 000 00 00
      </li>
      <li class="contact-item">
        <svg class="contact-icon" viewBox="0 0 12 12" aria-hidden="true">
          <path d="M1 2.5h10v1L6 6.6 1 3.5z"/>
          <path d="M1 4.7l5 3.1 5-3.1v4.8H1z"/>
        </svg>
        tovasel@lomu-grace.example
      </li>
      <li class="contact-item">
        <svg class="contact-icon" viewBox="0 0 12 12" aria-hidden="true">
          <circle cx="6" cy="6" r="5"/>
          <path d="M1 6h10M6 1c-2 2.8-2 7.2 0 10M6 1c2 2.8 2 7.2 0 10" stroke="#f4f4f3" stroke-width="0.9" fill="none"/>
        </svg>
        www.lomu-grace.example
      </li>
    </ul>
  </section>
</main>
</body>
</html>
```